Locksmith Business Cards

My father-in-law is in need of new business cards for his locksmith business and I need to impress him. Kindly help me out!

You can see the previous business card attached. It is a family run business in North Wales.

No individual names on the cards.

Key Things to Feature:
- The words "Prompt", "Local", "Reliable" (as you can see under the logo on the website)
- 24h Emergency Service
- Covering All of North Wales, the Wirral and Chester
- The color blue
- A key or a lock would be interesting (similar to the ones that come up when you google locksmith business card)

Optional (only if design includes bullet points, like the example below):
https://imgvaultcdn.net/samples/208314/55172/55172_3904821_208314_image.jpg
- Residential / Commercial / Automotive
- Alarms & Cameras
- Key Cutting & Safes

https://www.brynhafod-locksmiths.co.uk/

Industry/Entity Type

Locksmith

Contact Information for Business Card

01632 960 418
07700 900 362
brynhafodlocksmiths@mailvane.com
Brynhafod Locksmiths, The Willow Barn, 7 Tannery Rd., Llandudno LL99 4QX
www.brynhafod-locksmiths.co.uk

Requirements
Must have
• - The words "Prompt", "Local", "Reliable" (as you can see under the logo on the website)
• - 24h Emergency Service
• - Covering All of North Wales, the Wirral and Chester
Nice to have
• - A key or a lock would be interesting (similar to the ones that come up when you google locksmith business card)

```html
<!DOCTYPE html>
<html lang="en">
<head>
<meta charset="utf-8">
<title>Brynhafod Locksmiths – Business Cards</title>
<link rel="stylesheet" href="https://fonts.googleapis.com/css2?family=Oswald:wght@400;500;600&display=swap">
<style>
  :root {
    --stage: #e6e7eb;
    --navy: #1f2a6e;
    --navy-deep: #1b2563;
    --pattern-navy: #27347c;
    --periwinkle: #4a5ca6;
    --brand-blue: #2b3a8c;
    --ink: #2e2e33;
    --rule: #d4d4d8;
    --paper: #ffffff;
    --soft-white: #dfe3f5;
  }
  * { box-sizing: border-box; margin: 0; padding: 0; }
  html, body { width: 1200px; height: 782px; overflow: hidden; }
  body {
    background: var(--stage);
    font-family: "Oswald", sans-serif;
    position: relative;
  }
  .card {
    position: absolute;
    top: 236px;
    width: 540px;
    height: 309px;
    overflow: hidden;
    box-shadow: 0 6px 18px rgba(0,0,0,0.18);
  }
  .card--front { left: 40px; background: var(--paper); }
  .card--back { left: 620px; background: var(--navy); }

  /* Front */
  .brand {
    position: absolute;
    left: 36px;
    top: 92px;
    width: 210px;
  }
  .brand__row { display: flex; align-items: center; gap: 10px; }
  .brand__mark {
    width: 34px; height: 34px;
    background: var(--brand-blue);
    border-radius: 50%;
    flex: none;
  }
  .brand__name {
    color: var(--brand-blue);
    font-weight: 500;
    font-size: 25px;
    line-height: 1.02;
    text-transform: uppercase;
    letter-spacing: 0.3px;
  }
  .brand__tagline {
    margin-top: 8px;
    margin-left: 44px;
    color: var(--navy);
    font-weight: 600;
    font-size: 11.5px;
    letter-spacing: 0.6px;
  }
  .divider {
    position: absolute;
    left: 262px;
    top: 52px;
    width: 1px;
    height: 150px;
    background: var(--rule);
  }
  .contact {
    position: absolute;
    left: 282px;
    top: 52px;
    color: var(--ink);
    font-style: normal;
    font-weight: 500;
    font-size: 13px;
    line-height: 1.25;
  }
  .contact__address { margin-left: 22px; margin-bottom: 6px; }
  .contact__list { list-style: none; }
  .contact__item { display: flex; align-items: center; gap: 8px; font-size: 14px; line-height: 1.34; }
  .contact__icon { width: 13px; height: 13px; flex: none; fill: var(--ink); }
  .band { position: absolute; bottom: 0; }
  .band--dark {
    left: 0;
    width: 254px;
    height: 42px;
    background: var(--navy-deep);
    clip-path: polygon(0 0, 100% 45%, 100% 100%, 0 100%);
  }
  .band--light {
    left: 260px;
    right: 0;
    height: 24px;
    background: var(--periwinkle);
    clip-path: polygon(0 0, 100% 60%, 100% 100%, 0 100%);
  }

  /* Back */
  .back__pattern {
    position: absolute;
    inset: 0;
    background: linear-gradient(135deg, var(--pattern-navy), var(--navy));
  }
  .back__content {
    position: absolute;
    inset: 0;
    display: flex;
    flex-direction: column;
    align-items: center;
    justify-content: center;
    text-align: center;
    color: #fff;
  }
  .services {
    list-style: none;
    font-weight: 500;
    font-size: 16px;
    line-height: 1.3;
    letter-spacing: 0.3px;
  }
  .coverage {
    margin-top: 16px;
    font-size: 13px;
    font-weight: 400;
    line-height: 1.4;
    letter-spacing: 0.3px;
    color: var(--soft-white);
  }
  .coverage__emergency {
    font-weight: 600;
    font-size: 14px;
    color: #fff;
    text-transform: uppercase;
    letter-spacing: 0.8px;
  }
</style>
</head>
<body>
  <section class="card card--front" aria-label="Business card front">
    <div class="brand">
      <div class="brand__row">
        <span class="brand__mark" aria-hidden="true"></span>
        <span class="brand__name">Brynhafod<br>Locksmiths</span>
      </div>
      <p class="brand__tagline">Prompt. Local. Reliable</p>
    </div>

    <div class="divider" aria-hidden="true"></div>

    <address class="contact">
      <p class="contact__address">Brynhafod Locksmiths,<br>The Willow Barn, 7 Tannery<br>Rd., Llandudno LL99 4QX</p>
      <ul class="contact__list">
        <li class="contact__item">
          <svg class="contact__icon" viewBox="0 0 16 16" aria-hidden="true"><path d="M3 5c0-2 2-3 5-3s5 1 5 3l-2 1-1-1H6L5 6zM4 7h8l2 6H2z"/></svg>
          01632 960 418
        </li>
        <li class="contact__item">
          <svg class="contact__icon" viewBox="0 0 16 16" aria-hidden="true"><path d="M5 1h6a1 1 0 0 1 1 1v12a1 1 0 0 1-1 1H5a1 1 0 0 1-1-1V2a1 1 0 0 1 1-1zm0 2v9h6V3z"/></svg>
          07700 900 362
        </li>
        <li class="contact__item">
          <svg class="contact__icon" viewBox="0 0 16 16" aria-hidden="true"><path d="M1 3h14v10H1zm1.5 1.2L8 8.5l5.5-4.3z"/></svg>
          brynhafodlocksmiths@mailvane.com
        </li>
        <li class="contact__item">
          <svg class="contact__icon" viewBox="0 0 16 16" aria-hidden="true"><circle cx="8" cy="8" r="7"/></svg>
          www.brynhafod-locksmiths.co.uk
        </li>
      </ul>
    </address>

    <div class="band band--dark" aria-hidden="true"></div>
    <div class="band band--light" aria-hidden="true"></div>
  </section>

  <section class="card card--back" aria-label="Business card back">
    <div class="back__pattern" role="img" aria-label="Repeating pattern of small padlock motifs in a lighter navy"></div>
    <div class="back__content">
      <ul class="services">
        <li>Residential / Commercial / Automotive</li>
        <li>Alarms &amp; Cameras</li>
        <li>Key Cutting &amp; Safes</li>
      </ul>
      <p class="coverage">
        <span class="coverage__emergency">24h Emergency Service</span><br>
        Covering All of North Wales, the Wirral and Chester
      </p>
    </div>
  </section>
</body>
</html>
```